Podcast Cover Art for rebranded podcast - I have inspiration for the designs

I've had a podcast ("Paperboat Radio Hour") since 2018, but I'm in the process of rebranding it. I've attached the old cover art below, which I loved, but I don't need it to look like that at all. The rebranded podcast is called 'Open Window with Marnie Cole.' I've included the show description at the bottom. I've been working on various design options in Canva, but not obsessed with anything yet, but I'm attaching the ones I do like that I think just need some refining. My very favorite is the one labeled 'favorite_Open Window' so I wouldn't mind keeping that general idea but perfected by a designer. Ultimately, I want something cool, fairly clean, modern, eye catching. I'm into neutrals with maybe a pop of color, so think black, white, grey..maybe silver, and I love a pop of red..and I'm not opposed to other options for the pop color. The show is going to be inspiring, entertaining, and funny. Oh and one other idea I had but I'm not sure if it makes sense with the title and/or what the show is about..but a vinyl record with Open Window with Marnie Cole on it somehow, on a record player..not sure.

Ever wonder what it means to truly live authentically? Curious about how to embrace the unpredictability of life? Ready for some heartfelt and lighthearted conversations that inspire and entertain?
Join Marnie Cole as she dives into the raw, real, and unscripted moments of life. In each episode, Marnie brings candid conversations and genuine insights into the ups and downs we all experience. From personal growth and self-discovery to inspiring stories and valuable life lessons, "Open Window" is a space where authenticity reigns and spontaneity is celebrated.
Whether she's sharing her own journey or chatting with inspiring guests, Marnie invites you to explore the beauty of living life without a script. Expect honest reflections, thought-provoking discussions, and a refreshing perspective on navigating life's unpredictable path—all with a dash of fun and humor to keep things lively and entertaining. Step into the unscripted moments of life and tune in for a blend of depth and lightheartedness that will leave you inspired, smiling, and most importantly laughing.

Target Market(s)

25-50 year old women and men (primarily women)

Font styles to use
Sans Serif

Requirements
Should not have
• nothing too feminine or girly, nothing cheesy :)

```html
<!DOCTYPE html>
<html lang="en">
<head>
<meta charset="utf-8">
<title>Open Window with Marnie Cole — Podcast Cover</title>
<link rel="stylesheet" href="https://fonts.googleapis.com/css2?family=League+Spartan:wght@500;600;700&display=swap">
<style>
  :root {
    --page: #c9c9c9;
    --navy: #1a2331;
    --navy-ring: #1c2538;
    --teal: #0ccbaa;
    --outline: #1d4a52;
    --white: #ffffff;
    --photo-dark: #2f5a5a;
    --photo-light: #8fbdb3;
    --beach-dark: #6f6f6f;
    --beach-light: #e6e6e6;
  }
  * { margin: 0; padding: 0; box-sizing: border-box; }
  html, body {
    width: 1200px;
    height: 1033px;
    overflow: hidden;
    background: var(--page);
  }
  .canvas {
    position: relative;
    width: 1200px;
    height: 1033px;
    display: flex;
    align-items: center;
    justify-content: center;
  }
  .cover {
    width: 1000px;
    height: 1000px;
    display: block;
  }
  .cover text { font-family: "League Spartan", "Helvetica Neue", Arial, sans-serif; }
  .title-top { fill: var(--white); font-weight: 700; font-size: 164px; letter-spacing: -2px; }
  .title-main { fill: var(--teal); font-weight: 700; font-size: 164px; letter-spacing: -2px; }
  .title-echo { fill: none; stroke: var(--outline); stroke-width: 1.4; font-weight: 700; font-size: 164px; letter-spacing: -2px; }
  .echo-1 { opacity: 0.9; }
  .echo-2 { opacity: 0.6; }
  .echo-3 { opacity: 0.35; }
  .host-lead { fill: var(--teal); font-weight: 600; font-size: 50px; }
  .host-name { fill: var(--white); font-weight: 700; font-size: 78px; letter-spacing: -1px; }
</style>
</head>
<body>
<main class="canvas">
  <svg class="cover" viewBox="0 0 1000 1000" xmlns="http://www.w3.org/2000/svg">
    <defs>
      <linearGradient id="host-photo-tone" x1="0" y1="0" x2="0" y2="1">
        <stop offset="0" stop-color="var(--photo-dark)"/>
        <stop offset="1" stop-color="var(--photo-light)"/>
      </linearGradient>
      <linearGradient id="beach-photo-tone" x1="0" y1="0" x2="0" y2="1">
        <stop offset="0" stop-color="var(--beach-dark)"/>
        <stop offset="0.45" stop-color="var(--beach-light)"/>
        <stop offset="1" stop-color="#d4d4d4"/>
      </linearGradient>
      <clipPath id="host-cutout">
        <circle cx="705" cy="697" r="221"/>
        <rect x="540" y="340" width="330" height="360" rx="150"/>
      </clipPath>
    </defs>

    <rect class="cover-bg" width="1000" height="1000" fill="var(--navy)"/>

    <g class="title">
      <text class="title-top" x="86" y="196">OPEN</text>
      <text class="title-main" x="86" y="318">WINDOW</text>
      <text class="title-echo echo-1" x="86" y="440">WINDOW</text>
      <text class="title-echo echo-2" x="86" y="565">WINDOW</text>
      <text class="title-echo echo-3" x="86" y="690">WINDOW</text>
    </g>

    <g class="host-portrait">
      <circle class="host-ring" cx="705" cy="697" r="272" fill="var(--navy-ring)"/>
      <circle class="host-disc" cx="705" cy="697" r="221" fill="var(--teal)"/>
      <g clip-path="url(#host-cutout)">
        <rect role="img" aria-label="Portrait photo of host Marnie Cole, smiling, in teal duotone"
              x="540" y="340" width="330" height="600" fill="url(#host-photo-tone)"/>
      </g>
    </g>

    <g class="moment-photo">
      <circle cx="414" cy="551" r="124" fill="var(--navy)"/>
      <circle role="img" aria-label="Black and white photo of a woman in a sun hat standing at the shoreline"
              cx="414" cy="551" r="117" fill="url(#beach-photo-tone)"/>
    </g>

    <g class="host-credit">
      <text class="host-lead" x="97" y="753">with</text>
      <text class="host-name" x="97" y="839">MARNIE</text>
      <text class="host-name" x="97" y="906">COLE</text>
    </g>
  </svg>
</main>
</body>
</html>
```